Verlindo Magician

I want the business card for my business to give to people who watch that later I will be employed to show magic here is my website http://www.balsamomagicien.com/I want the interesting design , i am very opened for formal and informal, I watch a lot of design so don't stick to the common shape and form but i hope it can also be produced the thing to write on will be the same as in picture that i will upload , i also will upload the logo for you that so can be easy to useDenis CostilleMagicianMAGICIAN BALSAMO 17 rue des Tilleuls - 25000 BESANÇON contact@verlindoillusions.example tel. 0381 946 157 tel. 0674 219 503

```html
<!DOCTYPE html>
<html lang="fr">
<head>
<meta charset="utf-8">
<title>Verlindo Magician – Business Card</title>
<link rel="stylesheet" href="https://fonts.googleapis.com/css2?family=Jost:wght@300;400&display=swap">
<style>
  :root {
    --page-bg: #e8e5e1;
    --card-dark: #1d1d1f;
    --card-dark-tone: #252527;
    --card-light: #fbfafa;
    --pattern-grey: #efeeee;
    --pattern-pink: #f8ecec;
    --accent-red: #e2262b;
    --text-light: #d9d9d9;
    --text-dark: #111111;
    --divider: #6a6a6a;
    --portrait-dark: #141414;
    --portrait-mid: #3a3a3a;
  }
  * { margin: 0; padding: 0; box-sizing: border-box; }
  html, body { width: 1125px; height: 1200px; overflow: hidden; }
  body {
    background: var(--page-bg);
    font-family: "Jost", "Futura", sans-serif;
    font-weight: 300;
    position: relative;
  }
  .card {
    position: absolute;
    left: 150px;
    width: 825px;
    height: 470px;
    box-shadow: 0 3px 8px rgba(0,0,0,0.28);
    overflow: hidden;
  }
  .card--front { top: 98px; color: var(--text-light); }
  .card--back { top: 630px; }

  .card__texture {
    position: absolute;
    inset: 0;
  }
  .card--front .card__texture {
    background: radial-gradient(ellipse at 50% 45%, var(--card-dark-tone) 0%, var(--card-dark) 75%);
  }
  .card--back .card__texture {
    background: linear-gradient(135deg, var(--pattern-grey) 0%, var(--card-light) 35%, var(--pattern-pink) 60%, var(--card-light) 85%, var(--pattern-grey) 100%);
  }

  .identity {
    position: absolute;
    right: 475px;
    top: 188px;
    text-align: right;
  }
  .identity__name {
    color: var(--accent-red);
    font-size: 31px;
    font-weight: 300;
    letter-spacing: 0.2px;
    line-height: 1.1;
    text-transform: uppercase;
  }
  .identity__role { font-size: 21px; line-height: 1.2; }

  .divider {
    position: absolute;
    left: 373px;
    top: 175px;
    width: 1px;
    height: 102px;
    background: var(--divider);
  }

  .contacts {
    position: absolute;
    left: 392px;
    top: 170px;
    list-style: none;
  }
  .contacts__item {
    display: flex;
    align-items: center;
    height: 26.5px;
    font-size: 20px;
    letter-spacing: 0.3px;
  }
  .contacts__item--phone { font-size: 21px; }
  .icon { width: 18px; height: 18px; margin-right: 9px; flex: none; fill: var(--accent-red); }

  .address {
    position: absolute;
    left: 120px;
    top: 375px;
    display: flex;
    align-items: center;
    font-size: 20px;
    text-transform: uppercase;
    letter-spacing: 0.1px;
  }
  .address .icon { width: 16px; height: 22px; margin-right: 8px; }
  .address__street { text-transform: none; margin-left: 6px; }
  .address__city { text-transform: uppercase; }

  .portrait {
    position: absolute;
    left: 318px;
    top: 88px;
    width: 190px;
    height: 234px;
    border-radius: 60px 60px 18px 18px;
    background: linear-gradient(180deg, var(--portrait-mid) 0%, var(--portrait-dark) 55%);
  }

  .brand {
    position: absolute;
    left: 0; right: 0;
    top: 326px;
    text-align: center;
    color: var(--text-dark);
    font-size: 38px;
    font-weight: 300;
    letter-spacing: 1px;
    line-height: 1;
  }
</style>
</head>
<body>
  <section class="card card--front" aria-label="Card front">
    <div class="card__texture" role="img" aria-label="Faint dark card-suit pattern background"></div>
    <div class="identity">
      <h1 class="identity__name">Marc Ravoulet</h1>
      <p class="identity__role">Magician</p>
    </div>
    <div class="divider"></div>
    <ul class="contacts">
      <li class="contacts__item contacts__item--phone">
        <svg class="icon" viewBox="0 0 24 24"><path d="M6.6 10.8a15.2 15.2 0 0 0 6.6 6.6l2.2-2.2a1 1 0 0 1 1-.25 11.4 11.4 0 0 0 3.6.57 1 1 0 0 1 1 1V20a1 1 0 0 1-1 1A17 17 0 0 1 3 4a1 1 0 0 1 1-1h3.5a1 1 0 0 1 1 1c0 1.25.2 2.45.57 3.6a1 1 0 0 1-.25 1z"/></svg>
        0381 946 157
      </li>
      <li class="contacts__item contacts__item--phone">
        <svg class="icon" viewBox="0 0 24 24"><path d="M6.6 10.8a15.2 15.2 0 0 0 6.6 6.6l2.2-2.2a1 1 0 0 1 1-.25 11.4 11.4 0 0 0 3.6.57 1 1 0 0 1 1 1V20a1 1 0 0 1-1 1A17 17 0 0 1 3 4a1 1 0 0 1 1-1h3.5a1 1 0 0 1 1 1c0 1.25.2 2.45.57 3.6a1 1 0 0 1-.25 1z"/></svg>
        0674 219 503
      </li>
      <li class="contacts__item">
        <svg class="icon" viewBox="0 0 24 24"><rect x="2" y="6" width="20" height="13"/><path d="M2 6l10 7.5L22 6" fill="none" stroke="#1d1d1f" stroke-width="1.8"/></svg>
        contact@verlindoillusions.example
      </li>
      <li class="contacts__item">
        <svg class="icon" viewBox="0 0 24 24"><circle cx="12" cy="12" r="10"/><path d="M7 8c2 0 3 1 3 3s-2 2-2 4 1 3 1 4M14 4c0 2 1 3 3 3s2 2 1 4-2 1-3 3 1 4 1 5" fill="none" stroke="#1d1d1f" stroke-width="1.6"/></svg>
        www.verlindoillusions.example
      </li>
    </ul>
    <p class="address">
      <svg class="icon" viewBox="0 0 16 22"><path d="M8 0a8 8 0 0 0-8 8c0 6 8 14 8 14s8-8 8-14a8 8 0 0 0-8-8zm0 11a3 3 0 1 1 0-6 3 3 0 0 1 0 6z"/></svg>
      Magician Verlindo<span class="address__street">17 rue des Tilleuls - 25000 <span class="address__city">Besançon</span></span>
    </p>
  </section>

  <section class="card card--back" aria-label="Card back">
    <div class="card__texture" role="img" aria-label="Light card-suit pattern background in soft grey and pink"></div>
    <div class="portrait" role="img" aria-label="Black and white illustration of the magician holding a playing card"></div>
    <p class="brand">Verlindo Magician</p>
  </section>
</body>
</html>
```